Stage Design Company Business Card

We are looking to step up up our business card design for our team.

We are a Full service Design and Consultation company for Stage and TV with an emphasis in Theatrical Lighting.

We like our materials to be clean and modern with solid colors free of patterns and gradients. Our brand consists of 4 primary colors Purple, Black, Grey, and White. Provided is our Word Mark as well as our Symbol Logo.

We would like our cards to leave an impression beyond the information, show our attention to design and detail, and make our marks an easily recognized feature (together or apart) for our clients.

We need a warm approachable comfortable feel for some clients, and a professional flair for the board member type clients.

Attached are our brand elements, and our existing cards to give a sense of our style and a glipse at the information we provide on our cards.

Target Market(s)

broad client base from church leaders to high school teachers and architects.

Industry/Entity Type

Business

Contact Information for Business Card

We format our phone number with periods not parenthesis or dashes. Information will be edited for each of our team members, and team member specific cards are not part of this scope, but rather a template so to speak.

Font styles to use
Sans Serif

Colors
6b449b
ffffff
000000
333333
aaaaaa

Requirements
Must have
• Wordmark and logo mark present (does not need to exist on the same side of card)
• Brand Colors,
• Name, Phone, Email, Address.
• Unique choices that make someone stop and take a second look
Nice to have
• It would be nice to somehow convey what we DO, as our brand name does not lend itself to this, outside of an obvious tagline though.....
• social media if not crowded. all of our handles match (instagram, twitter, facebook)
Should not have
• "clipart"

```html
<!DOCTYPE html>
<html lang="en">
<head>
<meta charset="utf-8">
<title>Orven Business Card</title>
<link rel="stylesheet" href="https://fonts.googleapis.com/css2?family=Open+Sans:wght@400;600&display=swap">
<style>
  :root {
    --backdrop: #3a3330;
    --card: #0b0b0b;
    --ink: #ffffff;
    --ink-soft: #e6e6e6;
    --silver: #c9c9c9;
    --brand-purple: #6b449b;
    --shadow: rgba(0, 0, 0, 0.55);
  }
  * { margin: 0; padding: 0; box-sizing: border-box; }
  html, body {
    width: 1200px;
    height: 899px;
    overflow: hidden;
    background: var(--backdrop);
    font-family: "Open Sans", sans-serif;
  }
  .sheet {
    position: relative;
    width: 1200px;
    height: 899px;
    display: flex;
    align-items: center;
    justify-content: center;
    gap: 48px;
  }
  .card {
    position: relative;
    width: 530px;
    height: 303px;
    background: var(--card);
    box-shadow: 0 18px 40px var(--shadow);
    color: var(--ink);
  }
  /* Contact side */
  .card-contact .brand-mark {
    position: absolute;
    left: 58px;
    top: 126px;
    display: flex;
    align-items: center;
    gap: 12px;
    font-size: 30px;
    font-weight: 600;
    letter-spacing: 4px;
    color: var(--ink);
  }
  .brand-dot {
    width: 14px;
    height: 14px;
    border-radius: 50%;
    background: var(--brand-purple);
    flex: none;
  }
  .contact-block {
    position: absolute;
    left: 282px;
    top: 66px;
  }
  .person-name {
    font-size: 21px;
    font-weight: 400;
    line-height: 1.1;
  }
  .person-role {
    font-size: 12px;
    color: var(--ink-soft);
    margin-bottom: 16px;
  }
  .address {
    font-size: 13px;
    line-height: 1.35;
    color: var(--ink-soft);
    margin-bottom: 14px;
  }
  .contact-list { list-style: none; }
  .contact-list li {
    display: flex;
    align-items: center;
    gap: 10px;
    font-size: 13px;
    line-height: 1.5;
    color: var(--ink-soft);
  }
  .contact-list svg { width: 11px; height: 11px; flex: none; }
  /* Brand side */
  .card-brand {
    display: flex;
    flex-direction: column;
    align-items: center;
    justify-content: center;
    gap: 26px;
  }
  .card-brand .brand-dot {
    width: 22px;
    height: 22px;
  }
  .wordmark {
    font-size: 40px;
    font-weight: 400;
    letter-spacing: 22px;
    padding-left: 22px;
    line-height: 1;
    color: var(--silver);
  }
</style>
</head>
<body>
  <main class="sheet">
    <section class="card card-contact">
      <div class="brand-mark"><span class="brand-dot"></span>ORVEN</div>
      <div class="contact-block">
        <h1 class="person-name">Marcus Hale</h1>
        <p class="person-role">Managing Director</p>
        <p class="address">48 Lantern Row, Suite 2<br>Fairhaven, ST 40217.</p>
        <ul class="contact-list">
          <li>
            <svg viewBox="0 0 12 12" aria-hidden="true"><path d="M2.5 1h2l1 2.5-1.3 1a6 6 0 0 0 3.3 3.3l1-1.3 2.5 1v2c0 .6-.5 1-1 1A9 9 0 0 1 1.5 2c0-.5.4-1 1-1z" fill="var(--brand-purple)"/></svg>
            044.218.730.551
          </li>
          <li>
            <svg viewBox="0 0 12 12" aria-hidden="true"><rect x="1" y="2.5" width="10" height="7" fill="var(--brand-purple)"/><path d="M1 2.5l5 4 5-4" stroke="var(--card)" stroke-width="1" fill="none"/></svg>
            hello@orvenstage.com
          </li>
          <li>
            <svg viewBox="0 0 12 12" aria-hidden="true"><path d="M5 7l2-2M4.2 5.8L2.8 7.2a1.7 1.7 0 0 0 2.4 2.4l1.4-1.4M7.8 6.2l1.4-1.4a1.7 1.7 0 0 0-2.4-2.4L5.4 3.8" stroke="var(--brand-purple)" stroke-width="1.2" fill="none" stroke-linecap="round"/></svg>
            www.orvenstage.com
          </li>
        </ul>
      </div>
    </section>
    <section class="card card-brand">
      <span class="brand-dot"></span>
      <p class="wordmark">ORVEN</p>
    </section>
  </main>
</body>
</html>
```